New Service Brochure for The Brellford Spa

Hi All! We are looking for a new brochure design- tri-fold, double sided, and full color. We are a certified Tallow Spa for men and women in the heart of the Catskill Mountains of upstate New York. Our clients would describe us as laid back luxury with no pretensions and a home away from home vibe. Our font is Avalon. Key colors are black, white and gold. Looking for an inviting, clean, and modern/minimalist spread with a touch of elegance. No orchid imagery, please. I would like our "Tallow Spa" logo on cover, too please. Front cover image with with logo and "Tallow Spa" Sticker . Bottom of back with contact info. We would prefer massages go on left inside page, facials in middle and right inside, nails on back left, but we are open to new or different layout proposals. Thank you!

Target Market(s)

Men & Women.

Industry/Entity Type

Health And Wellness

Other font styles liked:
• Avalon is our signature font

Requirements
Must have
• Easy on the eyes.
Nice to have
• Negative space.
Should not have
• No orchids. Busy lines and wild colors.

```html
<!DOCTYPE html>
<html lang="en">
<head>
<meta charset="utf-8">
<title>The Brellford Spa – Service Brochure</title>
<link href="https://fonts.googleapis.com/css2?family=Questrial&display=swap" rel="stylesheet">
<style>
:root{
  --bg:#e4e4e4;
  --gold:#c9a55c;
  --gold-light:#dcbf83;
  --ink:#1b1b1b;
  --black:#141414;
  --charcoal:#4a4a4a;
  --white:#ffffff;
  --cream:#fbf8f3;
  --grey-text:#555;
  --desc-light:#e8e8e8;
}
*{margin:0;padding:0;box-sizing:border-box}
html,body{width:745px;height:1200px;overflow:hidden;background:var(--bg);font-family:"Questrial",sans-serif}
.sheet{position:absolute;left:53px;width:650px;height:506px;display:flex;box-shadow:0 10px 12px -6px rgba(0,0,0,.35)}
.sheet--outside{top:61px}
.sheet--inside{top:605px}
.panel{position:relative;width:216.6px;height:100%;overflow:hidden}
.dark{background:radial-gradient(ellipse at 60% 30%,var(--charcoal),var(--black) 75%);color:var(--white)}
.light{background:var(--white);color:var(--ink)}
.photo{position:absolute}
.band{position:absolute;left:0;right:0;height:5px;background:var(--gold)}
.heading{font-size:12px;color:var(--gold);font-weight:400}
.dark .heading{color:var(--gold-light)}
.intro{font-size:6.4px;line-height:1.35;color:var(--gold)}
.svc{margin-bottom:8px}
.svc-head{display:flex;font-size:5.8px;color:var(--gold);white-space:nowrap}
.on-dark .svc-head{color:var(--gold-light)}
.svc-head .leader{flex:1;border-bottom:1px dotted currentColor;margin:0 2px 1.5px}
.svc-desc{font-size:4.7px;line-height:1.35;margin-top:2px;color:var(--grey-text)}
.on-dark .svc-desc{color:var(--desc-light)}
.list{position:absolute}
.brand{text-align:center;font-weight:400;letter-spacing:1px;line-height:1}
.brand-name{font-size:30px}
.brand-tag{font-size:8.6px;margin-top:6px;letter-spacing:.2px}
.partner-mark{position:absolute;width:22px;height:22px;background:var(--gold)}
.btn{display:block;width:68px;padding:4px 0;background:var(--gold);color:var(--white);font-size:8.5px;text-align:center}
.contact{text-align:center;font-size:8.4px;line-height:1.6}
.hours{text-align:center;font-size:8.2px;line-height:1.75;color:var(--grey-text)}
.hours h3{font-size:8.4px;font-weight:400;letter-spacing:.5px}
.callout{position:absolute;left:11px;top:150px;width:205px;padding:6px 4px;border:1.5px solid var(--gold);background:var(--cream);text-align:center;font-size:12.4px;line-height:1.45;color:var(--ink)}
.badge{position:absolute;left:96px;top:205px;width:48px;height:48px;border-radius:50%;background:#4f8a2e;border:2px solid #2f5a1c}
.url{position:absolute;left:32px;top:483px;width:160px;padding:3px 0;background:var(--gold);color:var(--white);text-align:center;font-size:9.2px}
.wax{display:grid;grid-template-columns:1fr 1fr;font-size:6.2px;line-height:1.83;color:var(--white)}
.price{color:var(--gold-light)}
.sub{font-size:6px;color:var(--gold-light);letter-spacing:.2px}
.sub-intro{font-size:6.1px;line-height:1.28;color:var(--gold-light)}
</style>
</head>
<body>

<section class="sheet sheet--outside">

  <article class="panel light panel--nails">
    <div class="partner-mark" style="left:147px;top:14px" aria-hidden="true"></div>
    <h2 class="heading" style="position:absolute;left:7px;top:37px">Hands &amp; feet</h2>
    <p class="intro" style="position:absolute;left:7px;top:64px;width:202px;text-align:justify">Melt into a Pedicure Throne in our Nail Lounge. Our handmade soaks and scrubs are made in house with only the freshest natural and organic ingredients! Your hands and feet have never been loved like this! All nail services include nail and cuticle care, massage and polish of choice.</p>
    <div class="band" style="top:139px"></div>
    <div class="dark" style="position:absolute;left:0;top:144px;width:100%;height:278px"></div>
    <div class="list on-dark" style="left:7px;top:152px;width:203px">
      <div class="svc"><div class="svc-head">Organic Eight Greens Manicure<span class="leader"></span>$65</div><p class="svc-desc">Hydrate, smooth and clarify tired and abused hands. Stone crop cleansing oil, eight greens fizzofoliant, and lotus detox hand treatment. 55 minutes.</p></div>
      <div class="svc"><div class="svc-head">Hot Stone Manicure<span class="leader"></span>$65</div><p class="svc-desc">Heal and smooth tired hands with our signature Keratin and Copaiba hot herbal mitts. 55 minutes.</p></div>
      <div class="svc"><div class="svc-head">Reverse The Hands Of Time Manicure<span class="leader"></span>$75</div><p class="svc-desc">The name says it all. Smoothing lava scrub, brightening masque, and luscious tightening hand creme. 55 minutes.</p></div>
      <div class="svc"><div class="svc-head">Palo Santo Pedicure<span class="leader"></span>$85</div><p class="svc-desc">Includes our bespoke Bergamot and Balsam foot soak, refreshing Peppermint scrub, and Palo Santo Lotion. 55 minutes.</p></div>
      <div class="svc"><div class="svc-head">Brellford Spa Pedicure<span class="leader"></span>$75</div><p class="svc-desc">In addition to a classic pedicure, a soothing anti-inflammatory mud mask, paraffin wrap treatment and revitalizing foot; calf massage. Topped off with your choice of enamel. 55 minutes.</p></div>
      <div class="svc"><div class="svc-head">Mother of Dragonfruit Pedicure<span class="leader"></span>$85</div><p class="svc-desc">Breaker of calluses, Reliever of tired feet; Queen of the Cuticle, Mother of spring cleaning and perfectly polished toes... Soak. Scrub. Cuticle &amp; Nail Care. Hot stone foot and leg massage. Polish. The Throne. 55 minutes.</p></div>
      <div class="svc"><div class="svc-head">Grapefruit and Pine Pedicure<span class="leader"></span>$45</div><p class="svc-desc">A perfect pick me up for any feet that want to celebrate the season! Soak. Scrub. Cuticle &amp; Nail Care. Polish. Boom. 30 minutes.</p></div>
    </div>
    <div class="band" style="top:422px"></div>
    <div class="photo" role="img" aria-label="Hands receiving a pedicure with a soak and polish" style="left:0;top:427px;width:100%;height:79px;background:linear-gradient(120deg,#d9b9a3,#efe4dc 50%,#b8938a)"></div>
  </article>

  <article class="panel panel--contact">
    <div class="photo" role="img" aria-label="Bright spa bathroom with a marble soaking tub" style="left:0;top:0;width:100%;height:139px;background:linear-gradient(135deg,#f7e6d6,#e9cdb2 60%,#d7b08e)"></div>
    <div class="dark" style="position:absolute;left:0;right:0;top:139px;height:283px"></div>
    <div class="brand" style="position:absolute;left:0;right:0;top:182px;color:var(--white)">
      <div class="brand-name" style="font-size:25px">The Brellford Spa</div>
      <div class="brand-tag" style="margin-top:42px">a boutique spa for Men &amp; Women</div>
    </div>
    <span class="btn" style="position:absolute;left:74px;top:290px">GET IN TOUCH</span>
    <div class="contact" style="position:absolute;left:0;right:0;top:327px;color:var(--white)">
      <p style="margin-bottom:4px">(518) 555-0142</p>
      <p style="margin-bottom:4px">Info@TheBrellfordSpa.com</p>
      <p>42 Alder Hollow Road</p>
      <p>Brellford, NY 12400</p>
      <p>Just off Main Street!</p>
    </div>
    <div class="band" style="top:422px"></div>
    <div style="position:absolute;left:0;right:0;top:427px;bottom:0;background:var(--cream)">
      <div class="hours" style="margin-top:12px">
        <h3>HOURS</h3>
        <p>Thurs-Sat: 10am-6pm</p>
        <p>Sun-Mon: 10am-5pm</p>
        <p>Tues &amp; Wed: Closed</p>
      </div>
    </div>
  </article>

  <article class="panel light panel--cover">
    <div class="photo" role="img" aria-label="Woman relaxing during a head massage on a towel-draped spa bed" style="left:0;top:165px;width:100%;height:341px;background:linear-gradient(160deg,#f6efe6 5%,#e7cfb8 45%,#c99f80 75%,#a67c62)"></div>
    <div class="brand" style="position:absolute;left:0;right:0;top:34px;color:var(--ink)">
      <div class="brand-name" style="font-size:27px">The Brellford Spa</div>
      <div class="brand-tag" style="margin-top:12px">a boutique spa for Men &amp; Women</div>
    </div>
    <div class="callout">ESCAPE THE CONGESTION OF<br>EVERYDAY LIFE!</div>
    <div class="badge" role="img" aria-label="Tallow Spa certification seal"></div>
    <div class="url">www.thebrellfordspa.com</div>
  </article>
</section>

<section class="sheet sheet--inside">

  <article class="panel dark panel--massages">
    <h2 class="heading" style="position:absolute;left:8px;top:33px">Massages</h2>
    <p class="sub-intro" style="position:absolute;left:8px;top:53px;width:200px;font-size:6.4px">Tired, sore muscles, and exhausted minds are refreshed by the perfect massage customized to your individual needs.</p>
    <div class="list on-dark" style="left:8px;top:85px;width:200px">
      <div class="svc"><div class="svc-head">Swedish Massage<span class="leader"></span>$105/$160</div><p class="svc-desc">Relaxing and therapeutic. Ease tension and enhance circulation. Great for a first time massage or any spa veteran. 55min - 90min</p></div>
      <div class="svc"><div class="svc-head">Deep Tissue<span class="leader"></span>$115/$175</div><p class="svc-desc">A therapeutic combination of slow and deep pressure alleviates chronic pain, muscle fatigue, and limited range of motion. Muscle Therapy lotion or creme. 55min - 90min</p></div>
      <div class="svc"><div class="svc-head">Tension Tamer<span class="leader"></span>$125/$195</div><p class="svc-desc">Head, neck and shoulders. Deep Tissue with hot towels, muscle soothing oils, and cupping. 55min - 90min</p></div>
      <div class="svc"><div class="svc-head">Hot Stone<span class="leader"></span>$175</div><p class="svc-desc">Unforgettable. Warm basalt lava stones melt away all stress and tension in sore muscles and joints. The ultimate Après ski treat. 90min</p></div>
      <div class="svc"><div class="svc-head">Recovery<span class="leader"></span>$110/$170</div><p class="svc-desc">Specific to your athletic needs, whether pro or a weekend warrior. Relax, stretch, and recover. 55min - 90min</p></div>
      <div class="svc"><div class="svc-head">Recova Rapid Recovery Massage<span class="leader"></span>$135</div><p class="svc-desc">Ideal for runners, cyclists, hikers, skiers &amp; riders. Recover faster and feel better with Recova compression chamber sleeves. Mobilize fluid &amp; speed recovery for tired, sore and aching legs. Includes head, neck, shoulders, arm and hand massage. 55 minutes.</p></div>
      <div class="svc"><div class="svc-head">Prenatal<span class="leader"></span>$110</div><p class="svc-desc">Ultimate treat for Mother-to-be. Soothes aches and pains during pregnancy. Mother must be out of first trimester. 55 minutes.</p></div>
      <div class="svc"><div class="svc-head">Couples<span class="leader"></span>$210 &amp; up</div><p class="svc-desc">For lovebirds or loved ones. Relax and recoup with your favorite person. 55 or 90 minutes.</p></div>
    </div>
    <div class="band" style="top:382px"></div>
    <div class="photo" role="img" aria-label="Hot stone massage on a client's back" style="left:0;top:387px;width:100%;height:119px;background:linear-gradient(120deg,#c89a78,#ecd8c6 45%,#7a5a48)"></div>
  </article>

  <article class="panel light panel--facials">
    <div class="photo" role="img" aria-label="Woman with glowing skin touching her face" style="left:0;top:0;width:100%;height:140px;background:linear-gradient(135deg,#f2f2f2,#ead7c8 55%,#dcbfa9)"></div>
    <h2 class="heading" style="position:absolute;left:13px;top:158px">Facials</h2>
    <p class="intro" style="position:absolute;left:13px;top:178px;width:195px;text-align:justify">Featuring Verdell Organic Skincare products our organic and biodynamic facials are perfect for even the most sensitive skin!</p>
    <div class="list" style="left:13px;top:216px;width:195px">
      <div class="svc" style="margin-bottom:7px"><div class="svc-head">Detox Facial<span class="leader"></span>$135</div><p class="svc-desc">Increases oxygen and blood flow to dramatically reboot your skins natural healing abilities and reveal healthier skin. 55 minutes.</p></div>
      <div class="svc" style="margin-bottom:7px"><div class="svc-head">B.L.T. Facial<span class="leader"></span>$145</div><p class="svc-desc">Organic triple peel, also known as our "Runway Peel" because it leaves you glowing and ready for the red carpet immediately. 55 minutes.</p></div>
      <div class="svc" style="margin-bottom:7px"><div class="svc-head">Double Down Facial<span class="leader"></span>$165</div><p class="svc-desc">Organic triple peel, also known as our "Runway Peel" because it leaves you glowing and ready for the red carpet immediately. 55 minutes.</p></div>
      <div class="svc" style="margin-bottom:7px"><div class="svc-head">Organic Masque Montage<span class="leader"></span>$115</div><p class="svc-desc">Three layers of customized masques created exclusively for your skin type. Includes steam, cleanse, exfoliation, extractions, masques, massage, and moisturizer. 55 minutes.</p></div>
      <div class="svc" style="margin-bottom:7px"><div class="svc-head">Calm Skin Facial<span class="leader"></span>$125</div><p class="svc-desc">Combat redness, irritation and dryness. Gentle, yet effective for even the most sensitive skin types. Soothe, hydrate, and refresh. $125 - 55 mins</p></div>
      <div class="svc" style="margin-bottom:7px"><div class="svc-head">R&amp;R Facial<span class="leader"></span>$255 (Reg. $275)</div><p class="svc-desc">Our most dynamic results oriented facial, and the ultimate kick start to rebooting skin after a long summer of sunshine and heat... or making sure you are looking hot and 10 years younger when you see your ex. Microdermabrasion. Double Peel Facial. LED. (Light Emitting Diode) Boom. (as in WOW!) 90 minutes.</p></div>
      <div class="svc" style="margin-bottom:7px"><div class="svc-head">Mangosteen Facial<span class="leader"></span>$135</div><p class="svc-desc">Minimize pore size and surface build up with zero down time. Our organic lactic acid peel leaves skin smooth, clarified and glowing! Custom masque included. Ideal for all skin types. 55 minutes.</p></div>
      <div class="svc" style="margin-bottom:0"><div class="svc-head">Microdermabrasion<span class="leader"></span>$115</div><p class="svc-desc">Reduce wrinkles, scarring, discoloration, sun damage, large pores and age spots. Stimulate collagen and elastin production through diamond and crystal exfoliation. Best in series of six. 30min.</p></div>
    </div>
  </article>

  <article class="panel dark panel--hair">
    <h2 class="heading" style="position:absolute;left:12px;top:36px">Hair Removal</h2>
    <div style="position:absolute;left:12px;top:57px;width:200px">
      <p class="sub">ELECTROLYSIS</p>
      <p class="sub-intro" style="margin-top:2px">Say goodbye to unwanted and embarrassing hair with the only FDA approved method of Permanent Hair Removal. Great for men and women of all ages.</p>
      <div style="font-size:6.4px;line-height:1.85;margin-top:6px">
        <p>15 Minutes - <span class="price">$25</span></p>
        <p>30 Minutes - <span class="price">$45</span></p>
        <p>45 Minutes - <span class="price">$60</span></p>
        <p>60 Minutes - <span class="price">$75</span></p>
        <p>4 Hour Bonus Pack - <span class="price">$240</span></p>
      </div>
      <p class="sub" style="margin-top:23px">WAXING</p>
      <p class="sub-intro" style="margin-top:2px">Using only the best wax in the world, our custom blends of French and domestic waxes make for a flawless waxing experience. From eyebrows to Brazilians, your comfort and care is our priority.</p>
      <div class="wax" style="margin-top:14px">
        <span>Lips - <span class="price">$12</span></span><span>Brazilian - <span class="price">$65+</span></span>
        <span>Chin - <span class="price">$12</span></span><span>Chest - <span class="price">$30+</span></span>
        <span>Eyebrows - <span class="price">$15</span></span><span>Back - <span class="price">$35+</span></span>
        <span>Sideburns - <span class="price">$20</span></span><span>Underarm - <span class="price">$28</span></span>
        <span>Lower Half Leg - <span class="price">$30</span></span><span>Half Arm - <span class="price">$25</span></span>
        <span>Upper Half Leg - <span class="price">$40</span></span><span>Full Arm - <span class="price">$38</span></span>
        <span>Full Leg - <span class="price">$65</span></span><span>Feet - <span class="price">$10</span></span>
        <span>Bikini (top &amp; sides) - <span class="price">$50</span></span><span>Hands - <span class="price">$8</span></span>
      </div>
    </div>
    <div class="band" style="top:382px"></div>
    <div class="photo" role="img" aria-label="Guests celebrating with a dessert stand at a spa party" style="left:0;top:387px;width:100%;height:119px;background:linear-gradient(120deg,#f3e7dc,#e2c3a6 50%,#f6eee8)"></div>
  </article>
</section>

</body>
</html>
```